Venture Capital firm needs modern business cards

We are a Venture Capital firm within financial services/Asset management. The industry generally has basic business cards with black, blue and maybe green/yellow design elements.
Our firm has a four-colour swoosh logo. We are based in London and want to stand out, just a little bit!, from the crowd. Our company is called LORV Investments and the 'C' stands for collaboration thus using makerswarm is a natural portal for our business card design competition. Our logo came via makerswarm too!
We use 'Venture Partner in Asset Management' as our tagline and this is Trademark registered. We operate in a conservative industry and we should not overstep our mark. The logo is colorful as it is and therefore the rest of the design should not be too fanciful.
The objective is twofold: make our logo element stick and memorable with our audience, whilst representing a conservative yet young image.
Updates
The Business Card obviously needs a field for Name, Surname, Job Title, Adress fields: Street, City, Postcode, Country, telefone and cell number, website address, etc.
We have uploaded the ai file. We trust that these are OK. If not, please advise.
Reason: We have have been busy with a client engagement. We will set the project as Guaranteed in return for the troubles we cause. Apologies for the confusion.
Thank you all for these great and creative design suggestions. The team is very happy with a number of your ideas! We will be in touch tomorrow to give individual feedback before the project closes on Friday. We look forward to working with some of you to narrow down your creations. Thank you, LORV Investments team.
All,
Target Market(s)
Financial Services Professionals, Investors, Media, 35-70 years, mainly male, well educated
Industry/Entity Type
Conservative
Requirements
Must have
- We must make use of our logo and potential tagline 'Venture Partner in Asset Management' as we are establishing a new Brand and new company in the market.
We can use 'LORV', 'LORV Investments', and 'LORV Investments'+tagline 'Venture Partner in Asset Management' or simply the four-colour swoosh plus the name of the company as part of the text. (see files)
All design elements are available in black or grey-scale if required. (grey scale swoosh attached).
Due to regulation we must have the following wording on the card in small print 'LORV Investments is an Appointed Representative of Bramwell Holdings Partnership Limited, which is authorised by the Monetary Oversight Board'.
Nice to have
- We would consider designs that make use of different printing techniques such embossing/debossing, UV spot etc.
We attach our colour palette in the files section for your reference.
Should not have
- The font we use for our company name is 'EXO' so do not use a font style that clashes with the corporate fonts, please.
Do not use other design elements than the ones we provide in the file library as part of this project.

```html
<!DOCTYPE html>
<html lang="en">
<head>
<meta charset="utf-8">
<title>LORV Investments – Business Card</title>
<link rel="stylesheet" href="https://fonts.googleapis.com/css2?family=Open+Sans:wght@400;600;700&display=swap">
<style>
  :root {
    --stage: #e9e6e3;
    --card: #ffffff;
    --ink: #3a3a3c;
    --ink-soft: #6d6d70;
    --ink-faint: #9a9a9d;
    --accent-blue: #2aa6dc;
    --accent-green: #9ccc3a;
    --mark: #d3215f;
    --pattern-a: #f6f6f7;
    --pattern-b: #ebebed;
  }
  * { box-sizing: border-box; margin: 0; padding: 0; }
  html, body { width: 1200px; height: 868px; overflow: hidden; }
  body {
    background: var(--stage);
    font-family: "Open Sans", Arial, sans-serif;
    color: var(--ink);
    position: relative;
  }
  .card {
    position: absolute;
    width: 540px;
    height: 310px;
    background: var(--card);
    border-radius: 14px;
    box-shadow: 0 6px 18px rgba(0,0,0,0.18);
    overflow: hidden;
  }
  /* Front side */
  .card--front { left: 70px; top: 120px; }
  .front-pattern {
    position: absolute; inset: 0;
    background: radial-gradient(ellipse at 30% 40%, var(--pattern-b) 0%, var(--pattern-a) 45%, var(--card) 100%);
  }
  .front-brand {
    position: absolute; left: 110px; top: 110px;
    display: flex; align-items: center; gap: 22px;
  }
  .brand-dot {
    width: 64px; height: 64px; border-radius: 50%;
    background: var(--mark);
  }
  .brand-name {
    font-weight: 600; font-size: 58px; letter-spacing: 1px;
    color: var(--ink); line-height: 1;
  }
  .front-smallprint {
    position: absolute; left: 40px; right: 30px; bottom: 12px;
    font-size: 6.5px; color: var(--ink-faint); white-space: nowrap;
  }
  /* Back side */
  .card--back { left: 590px; top: 420px; }
  .back-brand { position: absolute; left: 62px; top: 78px; }
  .back-brand .logo-row { display: flex; align-items: center; gap: 10px; }
  .back-brand .brand-dot { width: 34px; height: 34px; }
  .back-brand .brand-name { font-size: 38px; }
  .tagline {
    margin: 4px 0 0 44px;
    font-size: 7.5px; color: var(--ink-soft);
  }
  .holder { position: absolute; left: 360px; top: 84px; }
  .holder-name { font-size: 21px; font-weight: 700; color: var(--ink); line-height: 1.1; }
  .holder-title { font-size: 12px; font-weight: 600; color: var(--accent-blue); }
  .divider {
    position: absolute; left: 90px; right: 90px; top: 190px; height: 1px;
    background: linear-gradient(90deg, transparent, var(--accent-green), transparent);
  }
  .contacts {
    position: absolute; left: 0; right: 0; top: 218px;
    display: flex; flex-direction: column; align-items: center; gap: 6px;
    font-size: 12px; color: var(--ink-soft);
  }
  .contact-row { display: flex; gap: 22px; }
  .contact { display: flex; align-items: center; gap: 6px; }
  .contact svg { width: 9px; height: 9px; fill: var(--ink-soft); }
</style>
</head>
<body>
  <section class="card card--front" aria-label="Business card front">
    <div class="front-pattern" role="img" aria-label="Faint grey brand swoosh pattern across the card background"></div>
    <div class="front-brand">
      <span class="brand-dot"></span>
      <span class="brand-name">LORV</span>
    </div>
    <p class="front-smallprint">LORV Investments is an Appointed Representative of Bramwell Holdings Partnership Limited, which is authorised by the Monetary Oversight Board</p>
  </section>

  <section class="card card--back" aria-label="Business card back">
    <div class="back-brand">
      <div class="logo-row">
        <span class="brand-dot"></span>
        <span class="brand-name">LORV</span>
      </div>
      <p class="tagline">Venture Partner in Asset Management</p>
    </div>
    <div class="holder">
      <p class="holder-name">Daniel Hartley</p>
      <p class="holder-title">SEO</p>
    </div>
    <div class="divider"></div>
    <div class="contacts">
      <div class="contact-row">
        <span class="contact">
          <svg viewBox="0 0 10 10"><path d="M5 0a3.3 3.3 0 0 0-3.3 3.3C1.7 6 5 10 5 10s3.3-4 3.3-6.7A3.3 3.3 0 0 0 5 0zm0 4.6a1.3 1.3 0 1 1 0-2.6 1.3 1.3 0 0 1 0 2.6z"/></svg>
          Address line, address line
        </span>
        <span class="contact">
          <svg viewBox="0 0 10 10"><path d="M2 0l2 2.4-1.2 1.3a6 6 0 0 0 3.5 3.5L7.6 6 10 8l-1.3 1.6C4.5 10 0 5.5.4 1.3z"/></svg>
          +44 00 000 000
        </span>
        <span class="contact">
          <svg viewBox="0 0 10 10"><path d="M3 0h4a1 1 0 0 1 1 1v8a1 1 0 0 1-1 1H3a1 1 0 0 1-1-1V1a1 1 0 0 1 1-1zm0 1.5v6h4v-6z"/></svg>
          +44 00 000 001
        </span>
      </div>
      <div class="contact-row">
        <span class="contact">
          <svg viewBox="0 0 10 10"><path d="M0 2h10v6H0zm1 .8v.4l4 2.6 4-2.6v-.4z"/></svg>
          d.hartley@lorvinvest.com
        </span>
        <span class="contact">
          <svg viewBox="0 0 10 10"><path d="M5 0a5 5 0 1 0 0 10A5 5 0 0 0 5 0zm0 1c.6.6 1.1 1.9 1.2 3.5H3.8C3.9 2.9 4.4 1.6 5 1zM1 5.5h1.8c.1 1.3.4 2.4.9 3.2A4 4 0 0 1 1 5.5zm0-1a4 4 0 0 1 2.7-3.2c-.5.8-.8 1.9-.9 3.2zm4 4.5c-.6-.6-1.1-1.9-1.2-3.5h2.4C6.1 7.1 5.6 8.4 5 9zm1.3-.3c.5-.8.8-1.9.9-3.2H9a4 4 0 0 1-2.7 3.2zM7.2 4.5c-.1-1.3-.4-2.4-.9-3.2A4 4 0 0 1 9 4.5z"/></svg>
          www.lorvinvest.com
        </span>
      </div>
    </div>
  </section>
</body>
</html>
```